ebook cover for The Heron & The Teapot (Plink!)

We would like an ebook cover for a post Ph.D. on Animal Totems book called The Heron and The Teapot. It is about human relationships and dating. Author is Marla Wendlow Ph.D.
I am thinking perhaps just typographic with a fancy custom italicized or handwriting kind of font that fills the whole page, or a picture that doesn't belittle the fairytale of love. Something cosmic.
The subtitle to guide people, small, is "on dating"

```html
<!DOCTYPE html>
<html lang="en">
<head>
<meta charset="utf-8">
<title>The Heron and The Teapot — On Dating</title>
<link rel="stylesheet" href="https://fonts.googleapis.com/css2?family=Kaushan+Script&family=Arimo:wght@400&family=Tinos:wght@400&display=swap">
<style>
  :root {
    --stage: #dcdcdc;
    --paper: #ffffff;
    --paper-shade: #f4f4f4;
    --title-red: #dc0028;
    --title-blue: #2f3f93;
    --ink: #111111;
    --heart: #d39aa6;
    --heart-soft: #d8a2ad;
  }
  html, body {
    margin: 0;
    padding: 0;
    width: 1200px;
    height: 800px;
    overflow: hidden;
    background: var(--stage);
  }
  .cover {
    position: absolute;
    left: 352px;
    top: 20px;
    width: 496px;
    height: 760px;
    background: linear-gradient(160deg, var(--paper) 55%, var(--paper-shade) 100%);
    box-shadow: 0 6px 18px rgba(0,0,0,0.12);
    overflow: hidden;
  }
  .heart {
    position: absolute;
    fill: var(--heart-soft);
  }
  .heart--pair { fill: var(--heart); }
  .title-line {
    position: absolute;
    left: 0;
    width: 100%;
    margin: 0;
    text-align: center;
    font-family: "Kaushan Script", cursive;
    font-weight: 400;
    line-height: 1;
    white-space: nowrap;
  }
  .title-line--the-top { top: 62px; font-size: 66px; color: var(--title-red); left: 40px; }
  .title-line--heron { top: 128px; font-size: 112px; color: var(--title-red); }
  .title-line--and { top: 272px; font-size: 58px; color: var(--ink); left: 20px; }
  .title-line--the-mid { top: 352px; font-size: 70px; color: var(--title-blue); left: 20px; }
  .title-line--teapot { top: 418px; font-size: 112px; color: var(--title-blue); }
  .subtitle {
    position: absolute;
    top: 618px;
    left: 0;
    width: 100%;
    margin: 0;
    text-align: center;
    font-family: "Arimo", sans-serif;
    font-size: 29px;
    letter-spacing: 5px;
    color: var(--title-red);
    text-transform: uppercase;
  }
  .author {
    position: absolute;
    top: 700px;
    left: 0;
    width: 100%;
    margin: 0;
    text-align: center;
    font-family: "Tinos", serif;
    font-size: 29px;
    letter-spacing: 5px;
    color: var(--ink);
  }
</style>
</head>
<body>
  <main class="cover">
    <svg class="heart" style="left:50px;top:60px" width="60" height="58" viewBox="0 0 100 92" role="img" aria-label="Small pink heart"><path d="M50 90 C10 60 0 40 0 25 C0 10 12 0 26 0 C38 0 46 8 50 16 C54 8 62 0 74 0 C88 0 100 10 100 25 C100 40 90 60 50 90 Z"/></svg>
    <svg class="heart" style="left:385px;top:55px" width="60" height="58" viewBox="0 0 100 92" role="img" aria-label="Small pink heart"><path d="M50 90 C10 60 0 40 0 25 C0 10 12 0 26 0 C38 0 46 8 50 16 C54 8 62 0 74 0 C88 0 100 10 100 25 C100 40 90 60 50 90 Z"/></svg>
    <svg class="heart" style="left:20px;top:240px" width="58" height="56" viewBox="0 0 100 92" role="img" aria-label="Small pink heart"><path d="M50 90 C10 60 0 40 0 25 C0 10 12 0 26 0 C38 0 46 8 50 16 C54 8 62 0 74 0 C88 0 100 10 100 25 C100 40 90 60 50 90 Z"/></svg>
    <svg class="heart" style="left:410px;top:240px" width="60" height="58" viewBox="0 0 100 92" role="img" aria-label="Small pink heart"><path d="M50 90 C10 60 0 40 0 25 C0 10 12 0 26 0 C38 0 46 8 50 16 C54 8 62 0 74 0 C88 0 100 10 100 25 C100 40 90 60 50 90 Z"/></svg>
    <svg class="heart heart--pair" style="left:85px;top:268px" width="320" height="200" viewBox="0 0 320 200" role="img" aria-label="Two overlapping large pink hearts">
      <path d="M95 188 C25 150 0 115 0 80 C0 50 25 35 50 35 C70 35 85 45 95 60 C105 30 130 0 160 10 C185 20 190 60 180 110 C170 150 140 175 95 188 Z" opacity="0.95"/>
      <path d="M185 195 C140 160 120 120 120 90 C120 60 140 25 170 25 C195 25 210 50 220 70 C235 55 255 45 275 45 C300 45 320 65 320 90 C320 130 270 170 185 195 Z" opacity="0.9"/>
    </svg>
    <svg class="heart" style="left:32px;top:598px" width="56" height="56" viewBox="0 0 100 92" role="img" aria-label="Small pink heart"><path d="M50 90 C10 60 0 40 0 25 C0 10 12 0 26 0 C38 0 46 8 50 16 C54 8 62 0 74 0 C88 0 100 10 100 25 C100 40 90 60 50 90 Z"/></svg>
    <svg class="heart" style="left:412px;top:620px" width="60" height="58" viewBox="0 0 100 92" role="img" aria-label="Small pink heart"><path d="M50 90 C10 60 0 40 0 25 C0 10 12 0 26 0 C38 0 46 8 50 16 C54 8 62 0 74 0 C88 0 100 10 100 25 C100 40 90 60 50 90 Z"/></svg>

    <h1 class="book-title">
      <span class="title-line title-line--the-top">The</span>
      <span class="title-line title-line--heron">Heron</span>
      <span class="title-line title-line--and">and</span>
      <span class="title-line title-line--the-mid">The</span>
      <span class="title-line title-line--teapot">Teapot</span>
    </h1>
    <p class="subtitle">On Dating</p>
    <p class="author">Marla Wendlow Ph.D.</p>
  </main>
</body>
</html>
```